Spring Style Exclusive Shopping Party for women

We need a postcard design for our Spring Shopping Event. Willow Lane is a women's apparel and accessories store featuring missy, petite and plus sizes. Event is Saturday, April 1 from 9am-10am. Looking for a twist on the spring shopping party idea. Attaching 2 postcards we have previously sent for this event and 2 ideas for what we are looking for in new postcard.

Target Market(s)

women 20+

Industry/Entity Type

Retail

Font styles to use
Serif

Requirements
Must have
• must be eye catching, have the logo, date and time of event,
Nice to have
• woman model

```html
<!DOCTYPE html>
<html lang="en">
<head>
<meta charset="utf-8">
<title>Willow Lane – Spring Shopping Event</title>
<link rel="stylesheet" href="https://fonts.googleapis.com/css2?family=Merienda:wght@700&family=Gelasio:wght@400&family=Source+Sans+3:wght@400;600&display=swap">
<style>
  :root {
    --sky-top: #bfe4f0;
    --sky-mid: #dcf0f7;
    --glow: #ffffff;
    --ink: #141a2c;
    --red: #f20d0d;
    --meadow-pink: #f6c3c0;
    --meadow-peach: #f7d9b0;
    --meadow-green: #d9eec8;
    --paper: #ffffff;
  }
  * { margin: 0; padding: 0; box-sizing: border-box; }
  html, body { width: 1200px; height: 1200px; overflow: hidden; background: var(--paper); }
  .canvas { position: relative; width: 1200px; height: 1200px; background: var(--paper); }
  .postcard {
    position: absolute; left: 0; top: 0; width: 1200px; height: 924px; overflow: hidden;
    background:
      radial-gradient(ellipse 300px 420px at 600px 330px, rgba(255,255,255,0.95), rgba(255,255,255,0) 100%),
      linear-gradient(180deg, var(--sky-top) 0%, var(--sky-mid) 45%, #eef8fb 75%, #f4fbf6 100%);
  }
  .meadow {
    position: absolute; left: 0; top: 384px; width: 1200px; height: 540px;
    background: linear-gradient(180deg, rgba(246,195,192,0) 0%, rgba(246,195,192,0.35) 40%, rgba(247,217,176,0.6) 70%, rgba(217,238,200,0.75) 100%);
    -webkit-mask-image: radial-gradient(ellipse 220px 380px at 620px 160px, transparent 55%, #000 100%);
            mask-image: radial-gradient(ellipse 220px 380px at 620px 160px, transparent 55%, #000 100%);
  }
  .brand {
    position: absolute; left: 0; width: 1200px; top: 78px; text-align: center;
    font-family: "Merienda", cursive; font-weight: 700; font-size: 86px; color: var(--ink);
  }
  .invite, .event-title {
    position: absolute; left: 0; width: 1200px; text-align: center;
    font-family: "Merienda", cursive; font-weight: 700; color: var(--ink);
  }
  .invite { top: 286px; font-size: 32px; }
  .event-title { top: 334px; font-size: 45px; }
  .date-day {
    position: absolute; left: 440px; top: 400px;
    font-family: "Merienda", cursive; font-weight: 700; font-size: 160px; line-height: 1; color: var(--red);
  }
  .date-month, .date-year {
    position: absolute; font-family: "Merienda", cursive; font-weight: 700; color: var(--ink); line-height: 1;
  }
  .date-month { left: 634px; top: 448px; font-size: 48px; }
  .date-year { left: 654px; top: 500px; font-size: 36px; }
  .weekday {
    position: absolute; left: 480px; top: 558px; width: 294px; height: 32px;
    background: linear-gradient(90deg, rgba(242,13,13,0) 0%, rgba(242,13,13,0.55) 55%, var(--red) 100%);
    font-family: "Merienda", cursive; font-weight: 700; font-size: 21px; color: #fff;
    text-align: right; padding-right: 12px; line-height: 32px;
  }
  .time {
    position: absolute; left: 440px; width: 400px; top: 592px; text-align: center;
    font-family: "Gelasio", serif; font-size: 28px; color: var(--ink); word-spacing: 4px;
  }
  .venue-at, .venue-name {
    position: absolute; left: 440px; width: 400px; text-align: center;
    font-family: "Merienda", cursive; font-weight: 700; color: var(--ink);
  }
  .venue-at { top: 652px; font-size: 28px; }
  .venue-name { top: 692px; font-size: 32px; }
  .contact { position: absolute; top: 822px; font-family: "Source Sans 3", sans-serif; color: var(--ink); line-height: 1.15; }
  .contact h3 { font-weight: 600; font-size: 23px; }
  .contact p { font-size: 16px; }
  .contact .phone { font-size: 26px; font-weight: 400; }
  .contact-store { right: 738px; text-align: right; }
  .contact-main { left: 520px; }
  .contact-rsvp { left: 717px; }
  .contact-rsvp .phone { font-size: 22px; margin-top: 6px; }
  .contact-rsvp .web { font-size: 16px; }
</style>
</head>
<body>
<div class="canvas">
  <section class="postcard">
    <div class="meadow" role="img" aria-label="Illustrated spring meadow with dandelions, flowers, butterflies and hummingbirds"></div>

    <div class="brand">Willow Lane</div>
    <div class="invite">Invites You to</div>
    <h1 class="event-title">Spring Shopping Event</h1>

    <div class="date-day">01</div>
    <div class="date-month">APRIL</div>
    <div class="date-year">2017</div>
    <div class="weekday">Saturday</div>
    <div class="time">9:00 am &nbsp;to &nbsp;10:00 am</div>

    <div class="venue-at">at</div>
    <div class="venue-name">MAPLE RIDGE ONLY</div>

    <div class="contact contact-store">
      <h3>MAPLE RIDGE</h3>
      <p>1820 N Orchard Dr</p>
      <p class="phone">309-555-0148</p>
    </div>
    <div class="contact contact-main">
      <h3>WILLOW LANE</h3>
      <p>45 S. Market St</p>
      <p>Fairbrook, IL 60000</p>
    </div>
    <div class="contact contact-rsvp">
      <h3>R.S.V.P</h3>
      <p class="phone">309-555-0148</p>
      <p class="web">www.willowlanestyle.com</p>
    </div>
  </section>
</div>
</body>
</html>
```